Corvell Keystone Lighting Commercial & Residential Landscape Lighting

Hello, I am looking for an Ad Design that I can use to promote ads on Plumora and other social media platforms. I want this ad to be a split screen ad meaning one photo at the top and one photo at the bottom to include a southern style home without outdoor landscape lighting & then the same picture at the bottom with outdoor landscape lighting. Add text to the graphic that talks about the difference landscape lighting does to your home. I want this ad to look professional and have professional design elements to the ad. I also have a logo I have uploaded below. We specialize in commercial grade outdoor landscape lighting, custom flag poles, outdoor audio, and we are locally and veteran owned. We offer lifetime warranty and quarterly maintenance on products.

```html
<!DOCTYPE html>
<html lang="en">
<head>
<meta charset="utf-8">
<title>Corvell Keystone Lighting – Social Ad</title>
<link rel="stylesheet" href="https://fonts.googleapis.com/css2?family=Poppins:wght@400;500;700&family=Oswald:wght@400&display=swap">
<style>
  :root {
    --page-bg: #ffffff;
    --ad-black: #000000;
    --gold: #e5a82a;
    --gold-deep: #d99a1e;
    --white: #ffffff;
    --ink: #000000;
    --glow: #1a1611;
  }
  * { box-sizing: border-box; margin: 0; padding: 0; }
  html, body {
    width: 1200px; height: 586px; overflow: hidden;
    background: var(--page-bg);
  }
  .ad {
    position: absolute; left: 330px; top: 23px;
    width: 540px; height: 540px;
    background: var(--ad-black);
    overflow: hidden;
    font-family: "Poppins", sans-serif;
  }
  .ad__glow {
    position: absolute; left: 320px; top: 150px;
    width: 260px; height: 260px; border-radius: 50%;
    background: radial-gradient(circle, var(--glow) 0%, rgba(26,22,17,0) 70%);
  }
  .photo { position: absolute; left: 0; width: 342px; }
  .photo--before {
    top: 0; height: 188px;
    background: linear-gradient(180deg, #5d6a73 0%, #4a5a44 40%, #3d5a2c 75%, #52693a 100%);
  }
  .photo--after {
    top: 193px; height: 190px;
    background:
      radial-gradient(ellipse 40% 35% at 55% 35%, rgba(240,170,70,0.75) 0%, rgba(240,170,70,0) 100%),
      radial-gradient(ellipse 50% 40% at 30% 70%, rgba(170,190,60,0.6) 0%, rgba(170,190,60,0) 100%),
      linear-gradient(180deg, #2d3d58 0%, #3a4a35 45%, #2f4a1e 80%, #000000 100%);
  }
  .brand {
    position: absolute; left: 350px; top: 70px; width: 180px;
    text-align: center;
    color: var(--gold);
    font-weight: 500; font-size: 19px; line-height: 1.25;
    letter-spacing: 1.5px; text-transform: uppercase;
  }
  .headline {
    position: absolute; left: 0; right: 0; top: 366px;
    text-align: center; color: var(--gold);
  }
  .headline__lead {
    color: var(--white); font-weight: 400; font-size: 26px; line-height: 1.2;
    padding-left: 30px;
  }
  .headline__main {
    font-size: 50px; line-height: 1.05; font-weight: 400; padding-left: 30px;
  }
  .headline__main strong { font-weight: 700; }
  .contact-bar {
    position: absolute; left: 0; bottom: 0; width: 100%; height: 58px;
    background: var(--gold);
    border-top: 5px solid var(--white);
    display: flex; align-items: center; justify-content: center; gap: 16px;
    font-family: "Oswald", sans-serif; font-size: 17px; color: var(--ink);
  }
  .contact-bar__item { display: flex; align-items: center; gap: 8px; }
  .contact-bar svg { width: 17px; height: 17px; fill: var(--ink); }
</style>
</head>
<body>
  <main class="ad">
    <div class="ad__glow"></div>
    <div class="photo photo--before" role="img" aria-label="Garden path and house at dusk without landscape lighting"></div>
    <div class="photo photo--after" role="img" aria-label="The same garden path and house at dusk lit by warm landscape lighting"></div>

    <div class="brand">Corvell Keystone Lighting</div>

    <div class="headline">
      <p class="headline__lead">Ready to See the Difference</p>
      <p class="headline__main"><strong>Lighting</strong> Makes?</p>
    </div>

    <footer class="contact-bar">
      <span class="contact-bar__item">
        <svg viewBox="0 0 24 24" aria-hidden="true"><path d="M2 5h20v14H2z M3.5 6.5 12 13l8.5-6.5" fill="none" stroke="#000" stroke-width="2"/></svg>
        (555)204-3318
      </span>
      <span class="contact-bar__item">
        <svg viewBox="0 0 24 24" aria-hidden="true"><path d="M6.6 10.8a15.1 15.1 0 0 0 6.6 6.6l2.2-2.2a1 1 0 0 1 1-.25 11.4 11.4 0 0 0 3.6.57 1 1 0 0 1 1 1V20a1 1 0 0 1-1 1A17 17 0 0 1 3 4a1 1 0 0 1 1-1h3.5a1 1 0 0 1 1 1c0 1.25.2 2.45.57 3.57a1 1 0 0 1-.25 1z"/></svg>
        hello@corvellkeystone.com
      </span>
    </footer>
  </main>
</body>
</html>
```